Android App Design Project

Hi my name is Nadir, and I'm an android developer. I'm searching for a professional designer that can design my app.I have already launched the app and you can find it in the apptrove bazaar.

Main Requirements
- 15 sport icons
- 6 android pages
- Action bar
- Buttons and other icons

You need to do all requirements to submit a design. I need the design in both JPEG format and Photoshop PSD format. If you are interested then please download the PDF file ,it will help you a lot.
The name of the app is "MATCH VIEW Classic" you can find it in Orbix Shelf.

NOTICE: You might read that the Payment is not guaranteed if I'm not happy with the design BUT if you make a good design and you win the contest, then you become my main designer that means if I want to change or add something to the design of the app in the future I return to you "the winner" directly to make the redesign and get paid for it.

Regards.
Skype: Fadi Hamoudi "fadi48"
E-mail: fadinadir@quillpost.net

Industry/Entity Type

Tv

Requirements
Must have
• - 15 sport icons
- 6 android pages
- Action bar
- Buttons and other icons

```html
<!DOCTYPE html>
<html lang="en">
<head>
<meta charset="utf-8">
<title>Match provider</title>
<link rel="stylesheet" href="https://fonts.googleapis.com/css2?family=PT+Sans+Narrow:wght@400;700&family=Ubuntu:wght@500&display=swap">
<style>
  :root {
    --bar-top: #f59a3c;
    --bar-bottom: #e8731a;
    --bar-edge: #c25a0e;
    --button-fill: #d8650f;
    --bg: #262626;
    --bg-light: #2d2d2d;
    --rule-dark: #121212;
    --rule-light: #3c3c3c;
    --text-white: #ffffff;
    --text-grey: #b9b9b9;
    --text-url: #cdcdcd;
    --accent-orange: #f07a1e;
    --league-red: #e0201c;
    --status-green: #3fae2a;
  }
  html, body { margin: 0; padding: 0; overflow: hidden; }
  body { width: 817px; height: 1200px; background: var(--bg); }
  .screen {
    position: relative; width: 817px; height: 1200px; overflow: hidden;
    background: repeating-linear-gradient(45deg, var(--bg) 0 3px, var(--bg-light) 3px 5px);
    font-family: "PT Sans Narrow", "Arial Narrow", sans-serif;
  }
  .action-bar {
    position: absolute; left: 0; top: 0; width: 817px; height: 102px;
    background: linear-gradient(var(--bar-top), var(--bar-bottom));
    border-bottom: 3px solid var(--bar-edge);
    box-sizing: border-box;
  }
  .action-bar__title {
    position: absolute; left: 0; right: 0; top: 0; line-height: 99px;
    text-align: center; color: var(--text-white);
    font-family: "Ubuntu", sans-serif; font-weight: 500; font-size: 43px;
  }
  .bar-button {
    position: absolute; top: 18px; width: 88px; height: 66px;
    border-radius: 12px; background: var(--button-fill);
    box-shadow: inset 0 2px 4px rgba(0,0,0,.35), 0 2px 0 rgba(255,255,255,.35);
  }
  .bar-button--back { left: 15px; }
  .bar-button--menu { left: 714px; }
  .bar-button svg { position: absolute; left: 0; top: 0; }
  .rule {
    position: absolute; left: 0; width: 817px; height: 3px;
    background: var(--rule-dark); border-bottom: 2px solid var(--rule-light);
  }
  .match { position: absolute; left: 25px; top: 130px; color: var(--text-white); font-weight: 700; font-size: 33px; line-height: 46px; }
  .match__vs { color: var(--accent-orange); }
  .match__type { position: absolute; left: 676px; top: 161px; color: var(--league-red); font-weight: 700; font-size: 33px; line-height: 46px; }
  .provider { position: absolute; left: 25px; font-size: 32px; line-height: 46px; }
  .provider__name { color: var(--text-grey); font-weight: 700; }
  .provider__link { color: var(--text-url); font-weight: 700; }
  .provider__status { color: var(--status-green); font-weight: 700; }
</style>
</head>
<body>
<div class="screen">
  <header class="action-bar">
    <div class="bar-button bar-button--back">
      <svg width="88" height="66" viewBox="0 0 88 66"><path d="M24 33 L42 18 L42 27 L64 27 L64 39 L42 39 L42 48 Z" fill="#fff"/></svg>
    </div>
    <div class="action-bar__title">Matche provider</div>
    <div class="bar-button bar-button--menu">
      <svg width="88" height="66" viewBox="0 0 88 66"><g fill="#fff"><rect x="24" y="18" width="40" height="7" rx="2"/><rect x="24" y="30" width="40" height="7" rx="2"/><rect x="24" y="42" width="40" height="7" rx="2"/></g></svg>
    </div>
  </header>

  <div class="match">Austrilia <span class="match__vs">vs</span> India<br>21.JAN.2013</div>
  <div class="match__type">LEAGUE</div>

  <div class="rule" style="top:274px"></div>
  <div class="provider" style="top:304px">
    <div class="provider__name">PROVIDER : BLAZE</div>
    <div class="provider__link">https://orbixshelf.net/store/apps/details?</div>
    <div class="provider__status">avilable</div>
  </div>

  <div class="rule" style="top:445px"></div>
  <div class="provider" style="top:475px">
    <div class="provider__name">PROVIDER : BLAZE</div>
    <div class="provider__link">https://orbixshelf.net/store/apps/details?</div>
    <div class="provider__status">avilable</div>
  </div>

  <div class="rule" style="top:618px"></div>
  <div class="provider" style="top:648px">
    <div class="provider__name">PROVIDER : BLAZE</div>
    <div class="provider__link">https://orbixshelf.net/store/apps/details?</div>
    <div class="provider__status">avilable</div>
  </div>

  <div class="rule" style="top:789px"></div>
  <div class="provider" style="top:819px">
    <div class="provider__name">PROVIDER : LINKCAST</div>
    <div class="provider__link">https://orbixshelf.net/store/apps/details?</div>
    <div class="provider__status">avilable</div>
  </div>

  <div class="rule" style="top:994px"></div>
  <div class="provider" style="top:1056px">
    <div class="provider__name">PROVIDER : BLAZE</div>
    <div class="provider__link">https://orbixshelf.net/store/apps/details?</div>
    <div class="provider__status">avilable</div>
  </div>
</div>
</body>
</html>
```